PillPeak website blog. Simple medical advice given in clear yes or no answers that save people money

I am developing a new web page that provides medical care cost savings at the consumers' fingertips. I need a web page that is clean, concise, and attractive for me to put my valuable medical information on. The information I provide is simple to obtain, yet very valuable to the consumer, and answered in a yes or no format. For example, A person may wonder if they need an antibiotic for cold like symptoms. Seeing a doctor for an antibiotic is very expensive. But with simple and clear advice at their fingertips, they can confidently avoid having to pay $200 or more to see a doctor and get an antibiotic. This is kind of like consumer reports for medical services.

Target Market(s)

People who are savvy shoppers and want to save money on healthcare. Likely younger ages between 21 and 60, who are mobile, readily use iphones, and want strong evidence based research to guide their decisions.

Industry/Entity Type

Coding

Number of Pages Required

Colors

Requirements
Must have
• A template on the "Question" and "Answer" page that can be edited many times that can be edited many times. The Confidence rating scale would need to be edited as well. The "Date Researched" the "PillPeak Pilluminate" and "References" all need to be able to be edited. This website must be very clear and simple to understand. A medical question is posed with a yes or no answer, then answered and given a confidence rating, we then tell them how much money they saved by going to our website.
Nice to have
• We want this to be slightly fun, vibrant, warm and inviting. This will be sometime later converted into an app format. Quirky, some humor to keep it interesting.
Should not have
• No sterile looking medical images. Not boring.

```html
<!DOCTYPE html>
<html lang="en">
<head>
<meta charset="utf-8">
<title>PillPeak</title>
<link rel="stylesheet" href="https://fonts.googleapis.com/css2?family=Poppins:wght@400;500;600&display=swap">
<style>
:root{
  --brand-blue:#1a7cc4;
  --nav-blue:#2a8fd0;
  --accent-red:#e0262c;
  --text-grey:#4a4a4a;
  --panel-grey:#e6e6e6;
  --panel-line:#d4d4d4;
  --footer-bg:#0f0f0f;
  --white:#ffffff;
  --arrow-blue:#2ba4e0;
}
*{margin:0;padding:0;box-sizing:border-box}
html,body{width:1200px;height:1012px;overflow:hidden;background:var(--white)}
body{font-family:'Poppins',sans-serif;position:relative}
.site-header{position:absolute;left:0;top:0;width:1200px;height:123px;background:var(--white)}
.brand{position:absolute;left:112px;top:38px;display:flex;align-items:center;gap:10px}
.brand-dot{width:40px;height:40px;border-radius:50%;background:var(--brand-blue)}
.brand-name{font-size:26px;font-weight:600;color:var(--brand-blue)}
.tagline{position:absolute;left:317px;top:48px;font-size:17px;color:var(--text-grey);letter-spacing:.3px;white-space:nowrap}
.tagline span{margin:0 7px}
.search{position:absolute;left:817px;top:33px;width:270px;height:50px;border:1px solid #d8d8d8;border-radius:25px;background:#f2f2f2}
.search-label{position:absolute;left:29px;top:15px;font-size:13.5px;color:#6b6b6b}
.search-btn{position:absolute;right:-1px;top:-1px;width:82px;height:50px;border-radius:25px;background:var(--brand-blue);display:flex;align-items:center;justify-content:center}
.main-nav{position:absolute;left:0;top:123px;width:1200px;height:60px;background:var(--nav-blue)}
.main-nav a{position:absolute;top:20px;font-size:15.5px;color:var(--white);text-decoration:none;white-space:nowrap}
.hero{position:absolute;left:0;top:183px;width:1200px;height:600px;background:linear-gradient(120deg,#3c8a95 0%,#2f7586 40%,#2b6a86 70%,#3a7ea2 100%)}
.side-menu{position:absolute;left:21px;top:88px;width:324px;background:var(--panel-grey)}
.side-menu li{list-style:none;height:62px;border-bottom:1px solid var(--panel-line);display:flex;align-items:center;padding-left:23px;font-size:16.5px;color:var(--text-grey)}
.side-menu li:last-child{border-bottom:none}
.side-menu svg{margin-right:20px;flex:none}
.hero-title{position:absolute;left:414px;top:228px;width:660px;text-align:center;color:var(--white);font-size:35px;font-weight:600;line-height:43px}
.arrow{position:absolute;top:276px;width:48px;height:48px;border-radius:50%;display:flex;align-items:center;justify-content:center}
.arrow-prev{left:17px;background:var(--white)}
.arrow-next{left:1123px;background:var(--arrow-blue)}
.site-footer{position:absolute;left:0;top:783px;width:1200px;height:229px;background:var(--footer-bg);color:var(--white)}
.disclaimer-title{position:absolute;left:111px;top:40px;font-size:22px;font-weight:600}
.disclaimer-text{position:absolute;left:112px;top:76px;width:380px;font-size:13.3px;line-height:24px}
.col-title{position:absolute;top:43px;font-size:17.5px;font-weight:500}
.email-box{position:absolute;left:541px;top:81px;width:176px;height:44px;border:2px solid var(--accent-red);border-radius:22px;display:flex;align-items:center;padding-left:21px;font-size:14.5px}
.email-box svg{position:absolute;right:27px;top:13px}
.ask-btn{position:absolute;left:849px;top:81px;width:240px;height:44px;border-radius:22px;background:var(--brand-blue);display:flex;align-items:center;padding-left:27px;font-size:14px;font-weight:500}
.legal{position:absolute;left:111px;top:183px;font-size:15px}
.social{position:absolute;top:179px;width:28px;height:28px;border-radius:50%;background:var(--white)}
</style>
</head>
<body>
<header class="site-header">
  <div class="brand"><div class="brand-dot"></div><div class="brand-name">PillPeak</div></div>
  <div class="tagline">CLEAR<span>•</span>VALUABLE<span>•</span>HEALTH ADVICE<span>•</span>RIGHT NOW</div>
  <div class="search">
    <div class="search-label">Search</div>
    <div class="search-btn"><svg width="22" height="22" viewBox="0 0 22 22"><circle cx="9" cy="9" r="6.5" fill="none" stroke="#fff" stroke-width="2.6"/><line x1="14" y1="14" x2="19.5" y2="19.5" stroke="#fff" stroke-width="2.8" stroke-linecap="round"/></svg></div>
  </div>
</header>
<nav class="main-nav">
  <a style="left:162px">Prev/screening</a>
  <a style="left:315px">Women's Health</a>
  <a style="left:476px">Men Health</a>
  <a style="left:600px">Meds</a>
  <a style="left:682px">Surgery</a>
  <a style="left:781px">Imaging</a>
  <a style="left:879px">Peds</a>
  <a style="left:957px">Contact US</a>
</nav>
<section class="hero" role="img" aria-label="Teal-toned photo of a stethoscope on a desk with heartbeat lines and health icons">
  <ul class="side-menu">
    <li><svg width="18" height="18" viewBox="0 0 18 18"><circle cx="9" cy="9" r="7.5" fill="none" stroke="#2a8fd0" stroke-width="1.4"/><path d="M7.5 5.5 11 9 7.5 12.5" fill="none" stroke="#2a8fd0" stroke-width="1.4"/></svg>Who We Are ?</li>
    <li><svg width="18" height="18" viewBox="0 0 18 18"><circle cx="9" cy="9" r="7.5" fill="none" stroke="#2a8fd0" stroke-width="1.4"/><path d="M7.5 5.5 11 9 7.5 12.5" fill="none" stroke="#2a8fd0" stroke-width="1.4"/></svg>How It Works</li>
    <li><svg width="18" height="18" viewBox="0 0 18 18"><circle cx="9" cy="9" r="7.5" fill="none" stroke="#2a8fd0" stroke-width="1.4"/><path d="M7.5 5.5 11 9 7.5 12.5" fill="none" stroke="#2a8fd0" stroke-width="1.4"/></svg>How We Know</li>
    <li><svg width="18" height="18" viewBox="0 0 18 18"><circle cx="9" cy="9" r="7.5" fill="none" stroke="#2a8fd0" stroke-width="1.4"/><path d="M7.5 5.5 11 9 7.5 12.5" fill="none" stroke="#2a8fd0" stroke-width="1.4"/></svg>Evidence Based Research</li>
    <li><svg width="18" height="18" viewBox="0 0 18 18"><circle cx="9" cy="9" r="7.5" fill="none" stroke="#2a8fd0" stroke-width="1.4"/><path d="M7.5 5.5 11 9 7.5 12.5" fill="none" stroke="#2a8fd0" stroke-width="1.4"/></svg>Dr.Whitmore</li>
    <li><svg width="18" height="18" viewBox="0 0 18 18"><circle cx="9" cy="9" r="7.5" fill="none" stroke="#2a8fd0" stroke-width="1.4"/><path d="M7.5 5.5 11 9 7.5 12.5" fill="none" stroke="#2a8fd0" stroke-width="1.4"/></svg>Who We Are Not</li>
    <li><svg width="18" height="18" viewBox="0 0 18 18"><circle cx="9" cy="9" r="7.5" fill="none" stroke="#2a8fd0" stroke-width="1.4"/><path d="M7.5 5.5 11 9 7.5 12.5" fill="none" stroke="#2a8fd0" stroke-width="1.4"/></svg>Are We Biased?</li>
  </ul>
  <div class="arrow arrow-prev"><svg width="14" height="16" viewBox="0 0 14 16"><path d="M9 2 3 8l6 6" fill="none" stroke="#222" stroke-width="2"/></svg></div>
  <h1 class="hero-title">Don't Spend another clinic on your health before checking us out !<br>It's Free</h1>
  <div class="arrow arrow-next"><svg width="14" height="16" viewBox="0 0 14 16"><path d="M5 2l6 6-6 6" fill="none" stroke="#fff" stroke-width="2"/></svg></div>
</section>
<footer class="site-footer">
  <h2 class="disclaimer-title">Disclaimer</h2>
  <p class="disclaimer-text">Lorem ipsum dolor sit amet, consectetur adipiscing elit, sed do eiusmod tempor incididunt ut labore et dolore magna aliqua.</p>
  <h3 class="col-title" style="left:539px">Become a PillPeak today!</h3>
  <div class="email-box">Enter Email<svg width="16" height="14" viewBox="0 0 16 14"><rect x="0" y="1" width="16" height="12" rx="2" fill="#fff"/><path d="M1 2.5 8 8l7-5.5" fill="none" stroke="#0f0f0f" stroke-width="1.4"/></svg></div>
  <h3 class="col-title" style="left:850px">Ask a Question Here!</h3>
  <div class="ask-btn">If it is Worthy,Will post it!</div>
  <p class="legal">© 2018 Copyrights | All Rights Reserved | Terms &amp; Conditions | Privacy Policy</p>
  <div class="social" style="left:971px" role="img" aria-label="Social network link"></div>
  <div class="social" style="left:1013px" role="img" aria-label="Social network link"></div>
  <div class="social" style="left:1052px" role="img" aria-label="Social network link"></div>
</footer>
</body>
</html>
```